DESIGN OF STATIONERY - TORVALE MED

WE WORK IN THE FIELD OF HEALTH (IMAGING: MRI - CT ETC.).
WE WOULD LIKE TO CREATE THE ENTIRE STATIONERY DESIGN : LETTERHEAD, BUSINESS CARD, CALENDAR, INVOICES, CD HOLDER, ETC.

Target Market(s)

PERSONS UNDERTAKING HEALTH EXAMINATIONS

```html
<!DOCTYPE html>
<html lang="en">
<head>
<meta charset="utf-8">
<title>TorvaleMed Stationery</title>
<link href="https://fonts.googleapis.com/css2?family=Open+Sans:wght@400;600&family=Roboto:wght@400&display=swap" rel="stylesheet">
<style>
  :root {
    --bg: #bcbbb7;
    --paper: #e3e3e3;
    --paper-shade: #d6d6d6;
    --brand-blue: #1b64a0;
    --brand-blue-dark: #175a8f;
    --brand-teal: #2a9d8f;
    --ink: #4a4a4a;
    --ink-soft: #5a5a5a;
  }
  * { box-sizing: border-box; margin: 0; padding: 0; }
  html, body { width: 1200px; height: 800px; overflow: hidden; }
  body { background: var(--bg); position: relative; font-family: "Open Sans", sans-serif; }

  .envelope-back { position: absolute; left: 158px; top: 122px; width: 410px; height: 282px; }
  .envelope-back svg { display: block; }

  .envelope-front {
    position: absolute; left: 158px; top: 444px; width: 410px; height: 206px;
    background: var(--paper); box-shadow: 0 6px 14px rgba(0,0,0,.18); overflow: hidden;
  }

  .brand { position: absolute; display: flex; flex-direction: column; }
  .brand__name { font-weight: 600; color: var(--brand-blue); line-height: 1; letter-spacing: .2px; }
  .brand__tag { font-weight: 400; color: var(--brand-blue); line-height: 1.2; }
  .envelope-front .brand { left: 22px; top: 24px; }
  .envelope-front .brand__name { font-size: 19px; }
  .envelope-front .brand__tag { font-size: 5.5px; margin-top: 2px; }

  .contact { position: absolute; font-family: "Roboto", sans-serif; color: var(--ink-soft); }
  .contact p { display: flex; align-items: center; gap: 3px; }
  .contact svg { flex: none; }
  .envelope-front .contact { left: 22px; top: 142px; font-size: 6.4px; line-height: 8.2px; }
  .envelope-front .contact .address { margin-bottom: 3px; display: block; }

  .letterhead {
    position: absolute; left: 655px; top: 147px; width: 390px; height: 502px;
    background: linear-gradient(to bottom, var(--paper-shade) 0 149px, #ececec 149px 320px, var(--paper-shade) 320px);
    box-shadow: 0 6px 16px rgba(0,0,0,.2);
  }
  .letterhead .brand { left: 33px; top: 30px; }
  .letterhead .brand__name { font-size: 17px; }
  .letterhead .brand__tag { font-size: 5px; margin-top: 2px; }
  .letterhead .contact { left: 277px; top: 23px; font-family: "Open Sans", sans-serif; font-size: 5.6px; line-height: 7.2px; }
  .letterhead .contact .address { display: block; margin-bottom: 2px; }

  .letter-body { position: absolute; left: 33px; top: 104px; width: 322px; color: var(--ink); font-size: 7.2px; line-height: 9.8px; }
  .letter-body p { text-align: justify; margin-bottom: 7px; }
  .letter-body .salutation { margin-bottom: 11px; }
  .letter-body .closing { margin-top: 3px; font-size: 7.4px; }
  .signature { position: absolute; left: 36px; top: 380px; width: 46px; height: 44px; background: #c9c9c9; border-radius: 2px; }

  .letter-band { position: absolute; left: 0; bottom: 0; width: 100%; height: 7px; display: flex; }
  .letter-band__blue { width: 272px; background: var(--brand-blue); clip-path: polygon(0 0, 100% 0, 97% 100%, 0 100%); }
  .letter-band__teal { flex: 1; background: var(--brand-teal); margin-left: 2px; clip-path: polygon(3% 0, 100% 0, 100% 100%, 0 100%); }
</style>
</head>
<body>

<div class="envelope-back">
  <svg width="410" height="282" viewBox="0 0 410 282" aria-label="Envelope back with open flap">
    <path d="M0 73 C10 35 20 5 45 2 C80 0 330 0 365 2 C390 5 400 35 410 73 L410 107 L0 107 Z" fill="var(--brand-blue-dark)"/>
    <rect x="0" y="73" width="410" height="34" fill="var(--brand-blue)"/>
    <path d="M0 80 C20 80 32 92 32 107 L32 282 L0 282 Z" fill="#e6e6e6"/>
    <path d="M410 80 C390 80 378 92 378 107 L378 282 L410 282 Z" fill="#e6e6e6"/>
    <path d="M0 282 L16 120 C18 110 25 106 35 106 L375 106 C385 106 392 110 394 120 L410 282 Z" fill="var(--paper-shade)"/>
  </svg>
</div>

<div class="envelope-front">
  <div class="brand">
    <span class="brand__name">TorvaleMed</span>
    <span class="brand__tag">Health Care Diagnostic</span>
  </div>
  <div class="contact">
    <span class="address">Harlow Court, 14 Fenmoor<br>Rd, London SE4 7QT</span>
    <p><svg width="6" height="6" viewBox="0 0 10 10"><path d="M2 1l2 2-1 1.5c.7 1.4 1.6 2.3 3 3L7.5 6l2 2-1.5 1.5C4.5 9 1 5.5.5 1.5Z" fill="var(--brand-blue)"/></svg>0200 555 0187</p>
    <p><svg width="6" height="6" viewBox="0 0 10 10"><rect x=".5" y="2" width="9" height="6" fill="none" stroke="var(--brand-blue)"/><path d="M.5 2l4.5 3.5L9.5 2" fill="none" stroke="var(--brand-blue)"/></svg>info@torvalemed.com</p>
    <p><svg width="6" height="6" viewBox="0 0 10 10"><circle cx="5" cy="5" r="4.3" fill="none" stroke="var(--brand-blue)"/><path d="M.7 5h8.6M5 .7c-2.5 2.5-2.5 6 0 8.6M5 .7c2.5 2.5 2.5 6 0 8.6" fill="none" stroke="var(--brand-blue)" stroke-width=".8"/></svg>www.torvalemed.com</p>
  </div>
</div>

<div class="letterhead">
  <div class="brand">
    <span class="brand__name">TorvaleMed</span>
    <span class="brand__tag">Health Care Diagnostic</span>
  </div>
  <div class="contact">
    <span class="address">Harlow Court, 14 Fenmoor<br>Rd, London SE4 7QT</span>
    <p><svg width="5" height="5" viewBox="0 0 10 10"><path d="M2 1l2 2-1 1.5c.7 1.4 1.6 2.3 3 3L7.5 6l2 2-1.5 1.5C4.5 9 1 5.5.5 1.5Z" fill="var(--brand-blue)"/></svg>0200 555 0187</p>
    <p><svg width="5" height="5" viewBox="0 0 10 10"><rect x=".5" y="2" width="9" height="6" fill="none" stroke="var(--brand-blue)"/><path d="M.5 2l4.5 3.5L9.5 2" fill="none" stroke="var(--brand-blue)"/></svg>info@torvalemed.com</p>
    <p><svg width="5" height="5" viewBox="0 0 10 10"><circle cx="5" cy="5" r="4.3" fill="none" stroke="var(--brand-blue)"/><path d="M.7 5h8.6M5 .7c-2.5 2.5-2.5 6 0 8.6M5 .7c2.5 2.5 2.5 6 0 8.6" fill="none" stroke="var(--brand-blue)" stroke-width=".8"/></svg>www.torvalemed.com</p>
  </div>

  <div class="letter-body">
    <p class="salutation">Dear customer,</p>
    <p>Lorem ipsum dolor sit amet, consectetur adipisicing elit, sed do eiusmod tempor incididunt ut labore et dolore magna aliqua. Ut enim ad minim veniam, quis nostrud exercitation ullamco laboris nisi ut aliquip ex ea commodo consequat. Duis aute irure dolor in reprehenderit in voluptate velit esse cillum dolore eu fugiat nulla pariatur. Excepteur sint occaecat cupidatat non proident, sunt in culpa qui officia deserunt mollit anim id est laborum.</p>
    <p>Lorem ipsum dolor sit amet, consectetur adipisicing elit, sed do eiusmod tempor incididunt ut labore et dolore magna aliqua. Ut enim ad minim veniam, quis nostrud exercitation ullamco laboris nisi ut aliquip ex ea commodo consequat. Duis aute irure dolor in reprehenderit in voluptate velit esse cillum dolore eu fugiat nulla pariatur. Excepteur sint occaecat cupidatat non proident, sunt in culpa qui officia deserunt mollit anim id est laborum.</p>
    <p>Lorem ipsum dolor sit amet, consectetur adipisicing elit, sed do eiusmod tempor incididunt ut labore et dolore magna aliqua. Ut enim ad minim veniam, quis nostrud exercitation ullamco laboris nisi ut aliquip ex ea commodo consequat. Duis aute irure dolor in reprehenderit in voluptate velit esse cillum dolore eu fugiat nulla pariatur. Excepteur sint occaecat cupidatat non proident, sunt in culpa qui officia deserunt mollit anim id est laborum.</p>
    <p>Lorem ipsum dolor sit amet, consectetur adipisicing elit, sed do eiusmod tempor incididunt ut labore et dolore magna aliqua. Ut enim ad minim veniam, quis nostrud exercitation ullamco laboris nisi ut aliquip ex ea commodo consequat. Duis aute irure dolor in reprehenderit.</p>
    <p class="closing">Yours Sincerely,</p>
  </div>
  <div class="signature" role="img" aria-label="Handwritten signature of the sender"></div>

  <div class="letter-band">
    <div class="letter-band__blue"></div>
    <div class="letter-band__teal"></div>
  </div>
</div>

</body>
</html>
```